Candle Rental Business seeks new website design

We need a new website design for a Candle hire business. The business rents out pillar candles for events such as weddings and corporate events. Our main target market is weddings. The business name is Hire a Lantern. The business name does not have a logo design.

We would like a website that is light in colours and creates a warm atmosphere. The design needs to be elegant and upmarket. There are different size candles that we hire out, ranging from 10cm diameter to 20cm diameter, flat, tall etc. All our candles are white in colour. Its just the size that differs.

We would also like to include a section for hiring out decor such as glassvases, candlebras, overlays and chairs sachets, chair covers. However, this is not the businesses main focus but an additional offering to customers.

Target Market(s)

Wedding venues and brides. Corporate events. School dances.

Industry/Entity Type

Hospitality

Logo Text

Hire a Lantern

Number of Pages Required

1 page

Font styles to use
Sans Serif
Script

Requirements
Must have
• Pictures of pillar candles. Plain white candles. The website must centre around candles.
Nice to have
• Different examples of candle centrepieces
Should not have
• Pictures must not be of brides. Pictures of surrounding is perferable.

```html
<!DOCTYPE html>
<html lang="en">
<head>
<meta charset="utf-8">
<title>Hire a Lantern</title>
<link href="https://fonts.googleapis.com/css2?family=Didact+Gothic&family=Montserrat:wght@500;600;700&family=Lato:wght@400;700&display=swap" rel="stylesheet">
<style>
:root{
  --orange:#f07d14;
  --orange-light:#f6a21c;
  --amber:#fbb216;
  --ink:#222;
  --grey:#666;
  --pale:#ececec;
  --dark:#2f2f2f;
  --white:#fff;
  --blue:#3b7bd6;
}
*{box-sizing:border-box;margin:0;padding:0}
html,body{width:1200px;height:3046px;overflow:hidden;background:var(--white)}
body{position:relative;font-family:'Lato',sans-serif;color:var(--ink)}
.abs{position:absolute}
.heading{font-family:'Didact Gothic',sans-serif;font-weight:400}
.bold-heading{font-family:'Montserrat',sans-serif;font-weight:600}
.btn{position:absolute;display:flex;align-items:center;justify-content:center;font-family:'Lato',sans-serif;font-size:15px;color:var(--white);background:var(--orange);height:38px}
.btn.white{background:var(--white);color:var(--orange)}
.btn.light{background:var(--orange-light)}

/* header */
.site-header{position:absolute;left:0;top:0;width:1200px;height:86px;background:var(--white)}
.brand{left:80px;top:26px;display:flex;align-items:center;gap:12px}
.brand-dot{width:26px;height:26px;background:var(--orange);border-radius:50%}
.brand-name{font-family:'Didact Gothic',sans-serif;font-size:36px;color:var(--ink)}
.account{right:80px;top:12px;display:flex;gap:34px;font-size:13px;color:var(--grey)}
.account span::before{content:"";display:inline-block;width:11px;height:11px;border:1px solid var(--grey);margin-right:7px;vertical-align:-1px}
.nav{left:680px;top:52px;display:flex;gap:0;font-family:'Didact Gothic',sans-serif;font-size:16px}
.nav a{color:var(--ink);text-decoration:none;padding:4px 10px;margin-right:22px}
.nav a.current{border:1px solid var(--orange);color:var(--orange)}

/* hero */
.hero{left:0;top:86px;width:1200px;height:534px;background:radial-gradient(ellipse at 50% 35%,#7a5a2c 0%,#3a2814 35%,#140c06 75%)}
.hero-title{left:0;top:372px;width:1200px;text-align:center;color:var(--white);font-family:'Montserrat',sans-serif;font-weight:600;font-size:40px}
.hero-sub{left:0;top:440px;width:1200px;text-align:center;color:var(--white);font-family:'Didact Gothic',sans-serif;font-size:30px}

/* about */
.section-title{left:0;width:1200px;text-align:center;font-size:40px;color:var(--ink)}
.about-text{left:95px;top:733px;width:1010px;text-align:center;font-size:13.5px;line-height:26px;color:var(--grey)}

/* feature panels */
.photo{position:absolute}
.panel-orange{left:600px;top:922px;width:600px;height:470px;background:var(--orange)}
.icon-ring{position:absolute;width:60px;height:60px;border:2px solid var(--white);border-radius:50%;display:flex;align-items:center;justify-content:center}
.panel-title{position:absolute;color:var(--white);font-size:38px}
.panel-text{position:absolute;color:var(--white);font-size:14px;line-height:29px}
.overlay-dark{left:46px;top:1430px;width:510px;height:396px;background:rgba(40,20,15,.35)}
.overlay-orange{left:640px;top:1430px;width:510px;height:396px;background:rgba(240,125,20,.85)}

/* steps */
.step-circle{position:absolute;width:150px;height:150px;border-radius:50%;display:flex;align-items:center;justify-content:center}
.step-label{position:absolute;width:200px;text-align:center;font-family:'Didact Gothic',sans-serif;font-size:20px;line-height:28px;color:var(--grey)}

/* decor */
.decor-band{left:0;top:2315px;width:1200px;height:385px;background:var(--pale)}
.decor-tile{position:absolute;top:2470px;width:252px;height:183px}
.decor-tile::after{content:"";position:absolute;inset:8px;border:1px solid rgba(255,255,255,.75)}
.decor-name{position:absolute;inset:0;display:flex;align-items:center;justify-content:center;text-align:center;color:var(--white);font-family:'Montserrat',sans-serif;font-weight:600;font-size:21px;line-height:28px;z-index:1}

/* footer */
.footer-rule{left:80px;top:2710px;width:1040px;height:1px;background:#ddd}
.foot-head{position:absolute;top:2738px;font-size:14px;font-weight:700;color:#333}
.foot-list{position:absolute;top:2776px;list-style:none;font-size:12px;color:var(--grey)}
.foot-list li{margin-bottom:19px}
.foot-list li::before{content:"•";margin-right:9px;color:#999}
.contact-row{position:absolute;left:302px;display:flex;gap:12px;font-size:12px;color:var(--grey);line-height:18px}
.field{position:absolute;left:652px;width:236px;border:1px solid #999;font-size:11px;color:#666;padding:4px 8px;background:var(--white)}
.social{position:absolute;left:1002px;display:flex;align-items:center;gap:10px;font-size:12px;color:var(--blue)}
.social i{width:30px;height:30px;border-radius:50%;display:block}
.bottom-bar{left:0;top:2990px;width:1200px;height:56px;background:var(--dark);color:#ddd;font-size:13px}
.cards{position:absolute;right:80px;top:21px;display:flex;gap:4px}
.cards i{display:block;width:26px;height:16px;background:#ddd;border-radius:2px}
</style>
</head>
<body>

<header class="site-header">
  <div class="abs brand"><span class="brand-dot"></span><span class="brand-name">Hire A Lantern</span></div>
  <div class="abs account"><span>log in</span><span>Register</span></div>
  <nav class="abs nav"><a class="current">Home</a><a>About Us</a><a>Our Products</a><a>Contact Us</a></nav>
</header>

<section>
  <div class="abs hero" role="img" aria-label="Candelabras with tall white pillar candles over an elegant reception table"></div>
  <h1 class="abs hero-title">There Are Two Ways of Spreading Light:</h1>
  <p class="abs hero-sub">To Be The Candle Or The Mirror That Reflects It</p>
  <div class="btn" style="left:496px;top:506px;width:206px;height:44px;font-size:18px">Rent Candles Now</div>
</section>

<section>
  <h2 class="abs heading section-title" style="top:668px">About Us</h2>
  <p class="abs about-text">We are a family owned and operated company and began making decorative candles for all occasions.&nbsp; All of our candles are individually hand made in our candle studio, situated in Kelmont, outside Harbourton.&nbsp; Our wax is local and of a very high quality, and dripless! Our wax is also made with a high melting point, which means it will not melt or bend in hot temperatures.</p>
  <div class="btn" style="left:542px;top:827px;width:117px">Read More</div>
</section>

<section>
  <div class="photo" style="left:0;top:922px;width:600px;height:470px;background:radial-gradient(ellipse at 45% 55%,#e9e2cf 0%,#8a7f62 40%,#3e2a22 85%)" role="img" aria-label="Glass hurricane candle centrepiece with white roses and greenery on a dinner table"></div>
  <div class="abs panel-orange"></div>
  <div class="icon-ring" style="left:654px;top:952px"><svg width="24" height="30" viewBox="0 0 24 30"><path d="M12 1c3 4 3 6 0 8-3-2-3-4 0-8z" fill="#fff"/><rect x="5" y="11" width="14" height="18" rx="2" fill="#fff"/></svg></div>
  <h3 class="bold-heading panel-title" style="left:654px;top:1020px">Hire Candles</h3>
  <p class="panel-text" style="left:654px;top:1082px;width:490px">Do you love using candles for your events but tired of sorting old used candles or buying expensive candles. Believe it or not you can now rent candles.&nbsp; All our candles come in different sizes and heights. You can add the ambience of candlelight to your event of wedding ceremony without the worry over dripping wax or open candle flames. Our candles do not melt.</p>
  <div class="btn white" style="left:654px;top:1283px;width:118px">Buy Now</div>
  <div class="btn light" style="left:784px;top:1283px;width:118px">More Info</div>
</section>

<section>
  <div class="photo" style="left:0;top:1392px;width:600px;height:470px;background:radial-gradient(ellipse at 35% 30%,#a3362a 0%,#4a1e18 45%,#1e120c 85%)" role="img" aria-label="Personalised pillar candles among festive red and green decorations"></div>
  <div class="abs overlay-dark"></div>
  <div class="photo" style="left:600px;top:1392px;width:600px;height:470px;background:radial-gradient(ellipse at 50% 50%,#c98a3c 0%,#5a3616 50%,#1a0f06 90%)" role="img" aria-label="Glowing white pillar candles in warm low light"></div>
  <div class="abs overlay-orange"></div>

  <div class="icon-ring" style="left:270px;top:1497px"><svg width="24" height="30" viewBox="0 0 24 30"><path d="M12 1c3 4 3 6 0 8-3-2-3-4 0-8z" fill="#fff"/><rect x="5" y="11" width="14" height="18" rx="2" fill="#fff"/></svg></div>
  <h3 class="bold-heading panel-title" style="left:0;width:600px;text-align:center;top:1572px">Personalised Candles</h3>
  <p class="panel-text" style="left:86px;width:430px;text-align:center;top:1636px;font-size:13.5px;line-height:28px">Hire a Lantern provides the opportunity to give a thoughtful, meaningful gift at a friendly price point. This unique gift conveys the time and care you put into creating it. The recipient will enjoy the beautiful presentation and be reminded...</p>
  <div class="btn" style="left:177px;top:1764px;width:118px">Buy Now</div>
  <div class="btn light" style="left:302px;top:1764px;width:118px">More Info</div>

  <div class="icon-ring" style="left:865px;top:1497px"><svg width="30" height="30" viewBox="0 0 30 30"><rect x="4" y="14" width="6" height="14" fill="#fff"/><rect x="12" y="9" width="6" height="19" fill="#fff"/><rect x="20" y="14" width="6" height="14" fill="#fff"/><circle cx="7" cy="10" r="2" fill="#fff"/><circle cx="15" cy="5" r="2" fill="#fff"/><circle cx="23" cy="10" r="2" fill="#fff"/></svg></div>
  <h3 class="bold-heading panel-title" style="left:600px;width:600px;text-align:center;top:1572px">Décor Hire</h3>
  <p class="panel-text" style="left:680px;width:430px;text-align:center;top:1636px;font-size:13.5px;line-height:28px">Hire a Lantern provides the opportunity to give a thoughtful, meaningful gift at a friendly price point. This unique gift conveys the time and care you put into creating it. The recipient will enjoy the beautiful presentation and be reminded...</p>
  <div class="btn white" style="left:772px;top:1764px;width:118px">Buy Now</div>
  <div class="btn light" style="left:898px;top:1764px;width:118px">More Info</div>
</section>

<section>
  <h2 class="abs heading section-title" style="top:1906px">How It Works</h2>
  <svg class="abs" style="left:0;top:1990px" width="1200" height="230" viewBox="0 0 1200 230">
    <g fill="none" stroke="#d8d8d8" stroke-width="3">
      <path d="M250 30 Q300 10 350 22"/><path d="M340 14 L352 22 L340 30"/>
      <path d="M555 200 Q600 215 650 190"/><path d="M636 188 L650 190 L644 202"/>
      <path d="M845 30 Q900 10 950 22"/><path d="M938 14 L950 22 L938 30"/>
    </g>
  </svg>
  <div class="step-circle" style="left:78px;top:2002px;background:var(--orange)"><svg width="56" height="76" viewBox="0 0 56 76"><path d="M28 2c7 9 7 14 0 18-7-4-7-9 0-18z" fill="#fff"/><rect x="10" y="26" width="36" height="48" rx="4" fill="#fff"/><g stroke="var(--orange)" stroke-width="3"><line x1="10" y1="40" x2="46" y2="40"/><line x1="10" y1="52" x2="46" y2="52"/><line x1="10" y1="64" x2="46" y2="64"/></g></svg></div>
  <div class="step-circle" style="left:375px;top:2002px;background:var(--amber)"><svg width="60" height="74" viewBox="0 0 60 74"><path d="M20 4a5 5 0 0 1 10 0v28l4-1v-6a5 5 0 0 1 10 0v8a5 5 0 0 1 10 2v22c0 10-8 16-18 16H30c-8 0-12-4-16-10L4 44a5 5 0 0 1 8-6l8 8z" fill="#fff"/></svg></div>
  <div class="step-circle" style="left:674px;top:2002px;background:var(--orange)"><svg width="76" height="60" viewBox="0 0 76 60"><rect x="4" y="14" width="64" height="40" rx="3" fill="#fff" transform="rotate(-10 36 34)"/><rect x="8" y="18" width="64" height="40" rx="3" fill="#fff" stroke="var(--orange)" stroke-width="3"/><circle cx="40" cy="38" r="9" fill="none" stroke="var(--orange)" stroke-width="3"/></svg></div>
  <div class="step-circle" style="left:971px;top:2002px;background:var(--amber)"><svg width="60" height="80" viewBox="0 0 60 80"><path d="M30 2c6 8 6 13 0 17-6-4-6-9 0-17z" fill="#fff"/><rect x="18" y="24" width="24" height="38" rx="3" fill="#fff"/><path d="M4 64h52l-6 10H10z" fill="#fff"/><path d="M50 70c8 0 8-8 0-8" fill="none" stroke="#fff" stroke-width="3"/></svg></div>
  <p class="step-label" style="left:53px;top:2196px">Choose your<br>Candle</p>
  <p class="step-label" style="left:350px;top:2196px">Book your<br>Candle</p>
  <p class="step-label" style="left:649px;top:2196px">Make<br>payment</p>
  <p class="step-label" style="left:946px;top:2196px">Light Up<br>Your Event</p>
</section>

<section>
  <div class="abs decor-band"></div>
  <h2 class="abs heading section-title" style="top:2362px">Other Decor Hires</h2>
  <div class="decor-tile" style="left:80px;background:linear-gradient(135deg,#2b3a44,#8fa3ad 55%,#1d2328)" role="img" aria-label="Clear glass vases with candles"><span class="decor-name">Glass Vases</span></div>
  <div class="decor-tile" style="left:342px;background:linear-gradient(135deg,#4a3e2c,#bda98a 55%,#3a2f20)" role="img" aria-label="Candelabras on a table"><span class="decor-name">Candle Bras</span></div>
  <div class="decor-tile" style="left:604px;background:linear-gradient(135deg,#222,#8c8c8c 55%,#1a1a1a)" role="img" aria-label="Chair overlays and sashes"><span class="decor-name">Overlays &amp;<br>Chairs Sachets</span></div>
  <div class="decor-tile" style="left:866px;background:linear-gradient(135deg,#3a2a30,#d7a6b2 55%,#4a3a3e)" role="img" aria-label="Chair covers with pink bows"><span class="decor-name">Chair Covers</span></div>
</section>

<footer>
  <div class="abs footer-rule"></div>
  <h4 class="foot-head" style="left:80px">Quick Links</h4>
  <ul class="foot-list" style="left:82px"><li>Home</li><li>About Us</li><li>Our Products</li><li>Contact Us</li></ul>

  <h4 class="foot-head" style="left:302px">Contact Details</h4>
  <div class="contact-row" style="top:2776px"><svg width="16" height="18" viewBox="0 0 16 18"><path d="M8 1a6 6 0 0 1 6 6c0 5-6 10-6 10S2 12 2 7a6 6 0 0 1 6-6z" fill="none" stroke="#777" stroke-width="1.5"/><circle cx="8" cy="7" r="2" fill="#777"/></svg><span>1/23 Lorem Ips Dolo, Consecer<br>werer Nonuy - 12345</span></div>
  <div class="contact-row" style="top:2822px"><svg width="16" height="18" viewBox="0 0 16 18"><path d="M4 2l3 4-2 2c1 2 3 4 5 5l2-2 4 3-2 3C8 17 1 10 2 4z" fill="#777"/></svg><span style="font-size:14px">123-456-7890</span></div>
  <div class="contact-row" style="top:2868px"><svg width="16" height="14" viewBox="0 0 16 14"><rect x="1" y="2" width="14" height="10" fill="none" stroke="#777" stroke-width="1.5"/><path d="M1 2l7 6 7-6" fill="none" stroke="#777" stroke-width="1.5"/></svg><span>info@companyname.com</span></div>

  <h4 class="foot-head" style="left:652px">Quick Inquiry</h4>
  <div class="field" style="top:2776px;height:32px">Name</div>
  <div class="field" style="top:2814px;height:32px">Phone</div>
  <div class="field" style="top:2852px;height:74px">Message</div>
  <div class="btn" style="left:650px;top:2934px;width:239px;height:32px;font-size:14px">Submit</div>

  <h4 class="foot-head" style="left:1002px">Follow Us</h4>
  <div class="social" style="top:2776px"><i style="background:#3b5998"></i>Friendly</div>
  <div class="social" style="top:2814px"><i style="background:#4aa9e8"></i>Chirper</div>
  <div class="social" style="top:2852px"><i style="background:#2a7fc0"></i>Linkwork</div>
  <div class="social" style="top:2890px"><i style="background:#d0402e"></i>Circles</div>

  <div class="abs bottom-bar">
    <span class="abs" style="left:80px;top:20px">Copyright © 2016 Hire A Lantern. All Rights Reserved.</span>
    <span class="abs" style="right:206px;top:20px">We Accept:</span>
    <div class="cards"><i></i><i></i><i></i><i></i></div>
  </div>
</footer>

</body>
</html>
```